A clean crisp business card for a Landscape Construction company. Designed to be easy to read contact/ info and also be appealing/interesting, unlike a traditional business card.

Industry/Entity Type

Landscape Construction

Contact Information for Business Card

Company name : Brambleford Landscape Construction, phone number: (877) 62Vista, website:Bramblefordyards.example, Email, sales@bramblefordyards.example

Requirements
Nice to have
• Luxurious finishes/ details…. Icons or emblems next to contact info
Should not have
• Clipart or general pictures

```html
<!DOCTYPE html>
<html lang="en">
<head>
<meta charset="utf-8">
<title>Brambleford Landscape Construction – Business Card</title>
<link href="https://fonts.googleapis.com/css2?family=Cinzel:wght@600&family=Arimo:wght@400&display=swap" rel="stylesheet">
<style>
  :root {
    --brand-blue: #2a6fc9;
    --brand-green: #8cc63f;
    --card-white: #ffffff;
    --card-black: #070707;
    --ink: #1c1c1c;
    --backdrop: #d9dadc;
  }
  * { margin: 0; padding: 0; box-sizing: border-box; }
  html, body { width: 1200px; height: 913px; overflow: hidden; }
  body {
    background: var(--backdrop);
    position: relative;
    font-family: "Arimo", Arial, sans-serif;
  }
  .card {
    position: absolute;
    width: 600px;
    height: 343px;
    border-radius: 12px;
    border-bottom: 4px solid var(--brand-green);
    border-right: 2px solid var(--brand-green);
    box-shadow: 0 6px 18px rgba(0,0,0,0.18);
  }
  .card--front { left: 80px; top: 90px; background: var(--card-white); }
  .card--back { left: 520px; top: 480px; background: var(--card-black); }

  .wordmark {
    position: absolute;
    display: flex;
    align-items: center;
    gap: 12px;
  }
  .wordmark__dot {
    width: 22px; height: 22px;
    border-radius: 50%;
    background: var(--brand-green);
    flex: none;
  }
  .wordmark__name {
    font-family: "Cinzel", serif;
    font-weight: 600;
    color: var(--brand-blue);
    line-height: 1.15;
    letter-spacing: 0.04em;
  }
  .card--front .wordmark { left: 36px; top: 128px; width: 250px; }
  .card--front .wordmark__name { font-size: 21px; }
  .card--back .wordmark { left: 110px; top: 128px; width: 400px; }
  .card--back .wordmark__name { font-size: 28px; }

  .divider {
    position: absolute;
    left: 300px; top: 80px;
    width: 2px; height: 170px;
    background: var(--brand-blue);
  }
  .person {
    position: absolute;
    left: 326px; top: 82px;
  }
  .person__name {
    font-family: "Cinzel", serif;
    font-weight: 600;
    font-size: 27px;
    color: var(--brand-blue);
    letter-spacing: 0.03em;
  }
  .person__title {
    font-family: "Cinzel", serif;
    font-weight: 600;
    font-size: 17px;
    color: var(--brand-green);
    margin-top: 2px;
  }
  .contact-list {
    list-style: none;
    margin-top: 20px;
  }
  .contact-list li {
    display: flex;
    align-items: center;
    gap: 7px;
    font-size: 14.5px;
    color: var(--ink);
    margin-bottom: 7px;
  }
  .contact-list svg { width: 12px; height: 12px; flex: none; }
</style>
</head>
<body>

<section class="card card--front" aria-label="Business card front">
  <div class="wordmark">
    <span class="wordmark__dot"></span>
    <span class="wordmark__name">Brambleford Landscape Construction</span>
  </div>
  <div class="divider"></div>
  <div class="person">
    <h1 class="person__name">Daniel Hart</h1>
    <p class="person__title">Director</p>
    <ul class="contact-list">
      <li>
        <svg viewBox="0 0 12 12" aria-hidden="true"><path d="M2.5 1 L4.5 1 L5.2 3.5 L4 4.5 Q5 7 7.5 8 L8.5 6.8 L11 7.5 L11 9.5 Q10 11 8.5 11 Q2 9.5 1 3.5 Q1 2 2.5 1Z" fill="var(--brand-green)"/></svg>
        (877) 62Vista
      </li>
      <li>
        <svg viewBox="0 0 12 12" aria-hidden="true"><rect x="1" y="2.5" width="10" height="7" fill="none" stroke="var(--brand-green)" stroke-width="1.2"/><path d="M1 2.5 L6 6.5 L11 2.5" fill="none" stroke="var(--brand-green)" stroke-width="1.2"/></svg>
        sales@bramblefordyards.example
      </li>
      <li>
        <svg viewBox="0 0 12 12" aria-hidden="true"><circle cx="6" cy="6" r="4.8" fill="none" stroke="var(--brand-green)" stroke-width="1.1"/><ellipse cx="6" cy="6" rx="2" ry="4.8" fill="none" stroke="var(--brand-green)" stroke-width="1"/><path d="M1.2 6 H10.8" stroke="var(--brand-green)" stroke-width="1"/></svg>
        www.bramblefordyards.example
      </li>
    </ul>
  </div>
</section>

<section class="card card--back" aria-label="Business card back">
  <div class="wordmark">
    <span class="wordmark__dot"></span>
    <span class="wordmark__name">Brambleford Landscape Construction</span>
  </div>
</section>

</body>
</html>
```